KDWB Business Card

Looking for a business card design to incorporate our branding. We want to only use the colors listing in the Branding Package (attached).
Updates

Target Market(s)

People who need their phone or device fixed.

Industry/Entity Type

Electronics

Contact Information for Business Card

Please use:

Brightwick Gadget Clinic LLC
4810 E Harlow Ridge Rd
Suite 417
San Antonio, TX 78163

Marcus Delgrove, Store Manager

(210) 555-0147

Requirements
Must have
• Must include the colors that are contained within the Branding Package PDF file.

```html
<!DOCTYPE html>
<html lang="en">
<head>
<meta charset="utf-8">
<title>Brightwick Gadget Clinic – Business Card</title>
<link href="https://fonts.googleapis.com/css2?family=Arimo:wght@400&display=swap" rel="stylesheet">
<style>
  :root {
    --backdrop: #9a9a9a;
    --card-white: #ffffff;
    --card-shade: #e9e9eb;
    --brand-orange: #e8431b;
    --charcoal: #444548;
    --ink: #2e2e30;
    --rule: #555558;
    --photo-light: #f1f2f5;
    --photo-mid: #dcdfe6;
  }
  * { margin: 0; padding: 0; box-sizing: border-box; }
  html, body { width: 1200px; height: 941px; overflow: hidden; }
  body {
    background: var(--backdrop);
    font-family: "Arimo", Arial, sans-serif;
    position: relative;
  }
  .card {
    position: absolute;
    top: 320px;
    width: 525px;
    height: 300px;
    overflow: hidden;
    box-shadow: 0 4px 10px rgba(0,0,0,0.25);
  }
  .card--front {
    left: 55px;
    background: linear-gradient(180deg, var(--card-white) 0%, var(--card-shade) 100%);
  }
  .card--back {
    left: 620px;
    background: var(--card-white);
  }
  .front-swoosh { position: absolute; inset: 0; }
  .brand {
    position: absolute;
    display: flex;
    align-items: center;
    gap: 12px;
    color: var(--brand-orange);
    font-weight: 400;
    white-space: nowrap;
  }
  .brand__square {
    background: var(--brand-orange);
    border-radius: 6px;
    flex: none;
  }
  .card--front .brand { left: 38px; top: 52px; font-size: 25px; }
  .card--front .brand__square { width: 34px; height: 34px; }

  .contact {
    position: absolute;
    left: 38px;
    top: 150px;
    display: flex;
    align-items: stretch;
  }
  .contact__person { padding-right: 22px; }
  .contact__name { font-size: 18px; color: var(--ink); }
  .contact__role { font-size: 11px; color: var(--brand-orange); margin-top: 3px; }
  .contact__phone {
    display: flex; align-items: center; gap: 8px;
    font-size: 15px; color: var(--ink); margin-top: 10px;
  }
  .contact__phone svg { flex: none; }
  .contact__divider { width: 1.5px; background: var(--rule); }
  .contact__address {
    padding-left: 22px;
    font-size: 12px;
    line-height: 1.45;
    color: var(--ink);
  }

  .back-photo {
    position: absolute; inset: 0;
    background: radial-gradient(ellipse at 40% 55%, var(--photo-mid) 0%, var(--photo-light) 55%, var(--card-white) 100%);
  }
  .card--back .brand {
    left: 50%; top: 50%;
    transform: translate(-50%, -50%);
    font-size: 32px;
  }
  .card--back .brand__square { width: 48px; height: 48px; border-radius: 9px; }
</style>
</head>
<body>
  <section class="card card--front" aria-label="Business card front">
    <svg class="front-swoosh" width="525" height="300" viewBox="0 0 525 300" aria-hidden="true">
      <path d="M412 0 C462 90 452 200 372 300 L525 300 L525 0 Z" fill="var(--charcoal)"/>
      <path d="M398 0 C448 90 438 200 358 300" fill="none" stroke="var(--brand-orange)" stroke-width="9"/>
    </svg>
    <div class="brand">
      <span class="brand__square"></span>
      <span class="brand__name">Brightwick Gadget Clinic</span>
    </div>
    <div class="contact">
      <div class="contact__person">
        <div class="contact__name">Marcus Delgrove</div>
        <div class="contact__role">Store Manager</div>
        <div class="contact__phone">
          <svg width="12" height="12" viewBox="0 0 12 12" aria-hidden="true">
            <rect width="12" height="12" fill="var(--brand-orange)"/>
            <rect x="4" y="2.5" width="4" height="7" rx="0.8" fill="none" stroke="#fff" stroke-width="1"/>
          </svg>
          <span>(210) 555-0147</span>
        </div>
      </div>
      <div class="contact__divider"></div>
      <div class="contact__address">
        4810 E Harlow Ridge Rd<br>
        Suite 417<br>
        San Antonio, TX 78163
      </div>
    </div>
  </section>

  <section class="card card--back" aria-label="Business card back">
    <div class="back-photo" role="img" aria-label="Faded photo of hands repairing an opened smartphone"></div>
    <div class="brand">
      <span class="brand__square"></span>
      <span class="brand__name">Brightwick Gadget Clinic</span>
    </div>
  </section>
</body>
</html>
```